Corvane Card

The logo is the Spanish flag colors I want a vibrant eye catching design with the yellow / red colors over either Navy or white background or black even ,
Would like a 2D feel to the logo with another lighter color logo under it look ,

Contact Information for Business Card

Corvane Flooring
Teodor Vashkin
Main Number
Cell Number
Fax Number

Website on the side of the card somewhere

Font styles to use
Sans Serif

Colors
ec1f27
ffc214

Requirements
Must have
• 2 logos feel one is bolder and the other one underneath very light

```html
<!DOCTYPE html>
<html lang="en">
<head>
<meta charset="utf-8">
<title>Corvane Flooring – Business Card</title>
<link href="https://fonts.googleapis.com/css2?family=Open+Sans:wght@400;700&display=swap" rel="stylesheet">
<style>
  :root {
    --backdrop: #3a3a3a;
    --card: #1c1c1c;
    --card-back: #1e1e1e;
    --edge: #e2b52a;
    --yellow: #ffc214;
    --red: #ec1f27;
    --text: #f2f2f2;
    --emboss: #3b3b3b;
  }
  * { box-sizing: border-box; margin: 0; padding: 0; }
  html, body { width: 1200px; height: 801px; overflow: hidden; }
  body {
    background: var(--backdrop);
    font-family: "Open Sans", Arial, sans-serif;
    display: flex;
    align-items: center;
    justify-content: center;
    gap: 44px;
  }
  .card {
    width: 540px;
    height: 309px;
    border: 2px solid var(--edge);
    border-radius: 2px;
    position: relative;
  }
  .card-front { background: var(--card); display: flex; }
  .card-back { background: var(--card-back); display: flex; align-items: center; justify-content: center; }

  .brand { display: flex; align-items: center; gap: 12px; }
  .brand-mark { width: 22px; height: 22px; }
  .brand-name { font-weight: 700; letter-spacing: 0.14em; text-transform: uppercase; font-size: 17px; }

  .front-brand {
    width: 52%;
    display: flex;
    align-items: center;
    justify-content: center;
  }
  .front-brand .brand-mark { background: var(--red); }
  .front-brand .brand-name { color: var(--yellow); }

  .front-contact {
    flex: 1;
    border-left: 1px solid var(--edge);
    margin: 30px 0 110px;
    padding: 12px 0 0 22px;
    color: var(--text);
    font-size: 12.5px;
    line-height: 1.45;
  }
  .person-name { color: var(--yellow); font-weight: 700; font-size: 17px; text-transform: uppercase; line-height: 1.2; }
  .person-title { margin-bottom: 8px; }
  .address { margin-bottom: 8px; }
  .contact-list { list-style: none; }
  .contact-list li { display: flex; align-items: center; gap: 7px; }
  .contact-list svg { width: 10px; height: 10px; fill: var(--red); flex: none; }

  .back-brand .brand-mark { background: var(--emboss); }
  .back-brand .brand-name { color: var(--emboss); font-size: 24px; }
</style>
</head>
<body>
  <section class="card card-front" aria-label="Business card front">
    <div class="front-brand">
      <div class="brand">
        <span class="brand-mark"></span>
        <span class="brand-name">Corvane Flooring</span>
      </div>
    </div>
    <div class="front-contact">
      <p class="person-name">Teodor Vashkin</p>
      <p class="person-title">President</p>
      <p class="address">4180 Harborline Way<br>Seacrest CA 90417</p>
      <ul class="contact-list">
        <li><svg viewBox="0 0 10 10"><path d="M2 0h2l1 3-1.5 1a6 6 0 0 0 2.5 2.5L7 5l3 1v2a2 2 0 0 1-2 2A8 8 0 0 1 0 2a2 2 0 0 1 2-2z"/></svg>555-318-0472</li>
        <li><svg viewBox="0 0 10 10"><path d="M2 0h6v10H2zM3 1v7h4V1z"/></svg>555-318-0473</li>
        <li><svg viewBox="0 0 10 10"><path d="M2 0h5v3h3v7H0V3h2zM3 1v2h3V1zM2 5v3h6V5z"/></svg>555-318-0474</li>
        <li><svg viewBox="0 0 10 10"><path d="M0 2h10v6H0zM1 3l4 3 4-3z"/></svg>info@corvaneflooring.com</li>
        <li><svg viewBox="0 0 10 10"><circle cx="5" cy="5" r="5"/></svg>www.corvaneflooring.com</li>
      </ul>
    </div>
  </section>

  <section class="card card-back" aria-label="Business card back">
    <div class="brand back-brand">
      <span class="brand-mark"></span>
      <span class="brand-name">Corvane Flooring</span>
    </div>
  </section>
</body>
</html>
```